Lumbra Ember Oven Kitchen (restaurant)

Restaurant with a cool vibe.
We need a refresh of existing site. Appealing to a hip crowd of 25 or older age bracket (mid price to high small town). Constant changes food and cocktail menu. A vibing atmosphere with jazz funk hip music.
Must be able to scale for any device… phone/mobile device super important.
Instagram: @Lumbra.Bexwell
Website: lumbrabexwell.example

Target Market(s)

25-55 age group

Number of Pages Required

1 page

Font styles to use
Sans Serif

Requirements
Must have
• Simple to navigate. Simplicity is the key to all sophistication.

Links/Buttons
Menu
Gift Cards
Reservations
Take Out
Contact Us
Should not have
• Please, nothing generic looking… no cookie cutter look. Originality

```html
<!DOCTYPE html>
<html lang="en">
<head>
<meta charset="utf-8">
<title>Lumbra Ember Oven Kitchen</title>
<link href="https://fonts.googleapis.com/css2?family=Oswald:wght@400;500;600&family=Open+Sans:wght@400;600;700&display=swap" rel="stylesheet">
<style>
:root{
  --red:#e0090d;
  --red-dark:#9c0d0e;
  --ink:#222;
  --charcoal:#2b2b2b;
  --footer:#1f1f1f;
  --white:#fff;
  --star:#f2a53a;
}
*{box-sizing:border-box;margin:0;padding:0}
html,body{width:1200px;height:4418px;overflow:hidden}
body{font-family:"Open Sans",Arial,sans-serif;color:var(--ink);background:var(--white)}
.page{position:relative;width:1200px;height:4418px;overflow:hidden}
.abs{position:absolute}
.head{font-family:"Oswald",Arial,sans-serif;font-weight:500;text-transform:uppercase;letter-spacing:-.5px}
.center{text-align:center}
.rule{position:absolute;height:2px}
.rule.red{background:var(--red)}
.rule.light{background:var(--white)}

/* header + hero */
.hero{left:0;top:0;width:1200px;height:800px;
  clip-path:polygon(0 0,1200px 0,1200px 660px,600px 790px,0 660px);
  background:radial-gradient(circle at 70% 40%,#6b4a3a 0,#3b2a22 45%,#1f1a18 100%)}
.topbar{left:0;top:0;width:1200px;height:78px;background:rgba(20,20,20,.55)}
.logo{font-family:"Oswald",Arial,sans-serif;font-weight:600;color:var(--white);text-align:center;line-height:1}
.logo .name{font-size:36px;letter-spacing:2px}
.logo .sub{font-size:12px;letter-spacing:.5px;font-weight:400;margin-top:2px}
.nav a{position:absolute;top:29px;font-family:"Oswald",Arial,sans-serif;font-size:14px;color:var(--white);text-decoration:none;transform:translateX(-50%);white-space:nowrap}
.nav a.active{color:var(--red)}
.nav .underline{position:absolute;left:374px;top:76px;width:68px;height:3px;background:var(--white)}
.hero-frame{left:297px;top:249px;width:596px;height:217px;border:2px solid var(--white)}
.hero-kicker{left:0;top:290px;width:1200px;color:var(--white);font-size:40px;font-weight:400}
.hero-title{left:0;top:330px;width:1200px;color:var(--white);font-size:70px;font-weight:400;line-height:1.1}
.btn-red{background:var(--red);color:var(--white);font-family:"Oswald",Arial,sans-serif;text-transform:uppercase;display:flex;align-items:center;justify-content:center}
.hero-btn{left:494px;top:442px;width:202px;height:48px;font-size:18px}
.slide-arrow{width:52px;height:52px;border-radius:50%;background:rgba(255,255,255,.55);display:flex;align-items:center;justify-content:center}

/* take out */
.takeout-photo{left:0;top:640px;width:600px;height:680px;background:linear-gradient(160deg,#8fb3d6 0,#a8c3db 30%,#8b4a32 45%,#6e3a28 75%,#3c3c3c 100%)}
.takeout-panel{left:600px;top:640px;width:600px;height:680px;background:linear-gradient(180deg,#f2f2f2,#dcdcdc)}
.takeout-title{left:600px;top:858px;width:572px;font-size:46px}
.body-copy{font-size:15px;line-height:23px;color:#333}
.takeout-copy{left:660px;top:960px;width:452px}
.takeout-copy p+p{margin-top:8px}
.btn-outline{border:2px solid var(--ink);font-family:"Oswald",Arial,sans-serif;text-transform:uppercase;display:flex;align-items:center;justify-content:center;font-size:16px}
.takeout-btn{left:802px;top:1136px;width:170px;height:44px}

/* menu */
.menu-band{left:0;top:1260px;width:1200px;height:560px;
  clip-path:polygon(0 60px,600px 20px,1200px 60px,1200px 560px,0 560px);
  background:linear-gradient(100deg,#b70a0c 0,#ee0c10 40%,#e0090d 70%,#a00a0b 100%)}
.menu-title{left:0;top:1312px;width:1200px;color:var(--white);font-size:42px}
.menu-card{top:1423px;width:243px;height:269px;background:var(--red-dark)}
.menu-card .photo{width:243px;height:200px}
.menu-card .label{height:69px;color:var(--white);font-family:"Oswald",Arial,sans-serif;font-size:18px;text-transform:uppercase;text-align:center;padding-top:14px}
.menu-card .label i{display:block;width:70px;height:1px;background:var(--white);margin:8px auto 0}
.menu-btn{left:478px;top:1736px;width:232px;height:47px;border:2px solid var(--white);color:var(--white);font-family:"Oswald",Arial,sans-serif;font-size:16px;text-transform:uppercase;display:flex;align-items:center;justify-content:center}

/* reservation */
.res-dark{left:0;top:1800px;width:602px;height:583px;background:var(--charcoal)}
.res-photo{left:602px;top:1800px;width:598px;height:583px;clip-path:polygon(0 50px,598px 0,598px 583px,0 583px);background:linear-gradient(150deg,#c9b39a 0,#8a6a4e 35%,#4a3526 70%,#2b2119 100%)}
.res-title{left:0;top:1960px;width:676px;color:var(--white);font-size:38px}
.res-copy{left:118px;top:2060px;width:440px;color:#ddd}
.res-copy p+p{margin-top:8px}
.res-btn{left:252px;top:2213px;width:170px;height:45px;font-size:17px}

/* gift cards */
.gift-title{left:0;top:2442px;width:1200px;font-size:38px}
.gift-card{width:294px;height:275px;background:var(--white);border-radius:0 60px 0 0;box-shadow:0 6px 22px rgba(0,0,0,.14);text-align:center}
.gift-card .voucher{margin:36px auto 0;width:222px;height:108px}
.gift-card h3{font-family:"Oswald",Arial,sans-serif;font-weight:500;color:var(--red);font-size:21px;margin-top:16px;text-transform:uppercase}
.gift-card p{font-size:11px;line-height:16px;color:#444;margin:4px 28px 0}
.dots{left:566px;top:2864px}

/* testimonials */
.testi-band{left:0;top:2940px;width:1200px;height:540px;background:repeating-linear-gradient(90deg,#f4f4f4 0 118px,#e6e6e6 118px 120px)}
.testi-title{left:0;top:2988px;width:1200px;font-size:38px}
.testi-card{top:3111px;width:297px;height:258px;background:var(--white);box-shadow:0 4px 16px rgba(0,0,0,.1);padding:22px 38px 0 38px}
.testi-card h4{font-family:"Open Sans",Arial,sans-serif;font-weight:700;font-size:18px;margin-top:10px}
.testi-card p{font-size:11px;line-height:19px;color:#333;margin-top:6px}
.testi-card .who{font-size:11px;font-weight:600;margin-top:10px}
.stars{color:var(--star);font-size:13px;letter-spacing:1px}

/* contact */
.contact-photo{left:0;top:3480px;width:700px;height:560px;background:linear-gradient(135deg,#5b4538 0,#3a2e28 40%,#1e1a18 100%)}
.contact-red{left:0;top:3480px}
.contact-title{left:696px;top:3580px;color:var(--white);font-size:36px}
.contact-lines{left:696px;top:3656px;color:var(--white);font-size:18px;line-height:29px}
.contact-lines .gap{height:14px}
.contact-btn{left:703px;top:3877px;width:178px;height:48px;border:2px solid var(--white);color:var(--white);font-family:"Oswald",Arial,sans-serif;font-size:16px;text-transform:uppercase;display:flex;align-items:center;justify-content:center}
.to-top{left:1060px;top:4020px;width:40px;height:40px;border-radius:50%;background:var(--red);display:flex;align-items:center;justify-content:center}

/* footer */
.footer{left:0;top:4037px;width:1200px;height:381px;background:var(--footer)}
.foot-logo{left:140px;top:4100px;width:200px}
.foot-logo .name{font-size:40px}
.social{top:4194px;width:36px;height:36px;border-radius:50%;background:var(--red);border:2px solid var(--white)}
.foot-col h5{font-family:"Open Sans",Arial,sans-serif;font-weight:700;color:var(--white);font-size:14px;text-transform:uppercase}
.foot-col .underrule{display:block;width:40px;height:1px;background:var(--white);margin-top:8px}
.foot-col ul{list-style:none;margin-top:12px}
.foot-col li{color:#bbb;font-size:12px;line-height:24px}
.foot-col .small{font-size:11px;line-height:22px;display:flex;align-items:center;gap:8px}
.foot-rule{left:160px;top:4345px;width:920px;height:1px;background:#3a3a3a}
.copyright{left:167px;top:4365px;color:#aaa;font-size:11px}
.legal{top:4365px;color:#aaa;font-size:11px}
</style>
</head>
<body>
<div class="page">

  <!-- Take out (under hero) -->
  <div class="abs takeout-photo" role="img" aria-label="Photo of the brick restaurant building on a street corner"></div>
  <div class="abs takeout-panel"></div>

  <!-- Hero -->
  <div class="abs hero" role="img" aria-label="Photo of wood fired tacos with red cabbage and sauce"></div>
  <svg class="abs" style="left:0;top:0" width="1200" height="820" viewBox="0 0 1200 820" aria-hidden="true">
    <polygon points="430,752 600,790 770,752 600,800" fill="#c4080b"/>
  </svg>
  <div class="abs topbar"></div>
  <div class="abs logo" style="left:88px;top:16px;width:206px"><div class="name">LUMBRA</div><div class="sub">Ember Oven Kitchen</div></div>
  <nav class="nav">
    <a class="active" href="#" style="left:408px">HOME</a>
    <a href="#" style="left:519px">ABOUT US</a>
    <a href="#" style="left:632px">MENU</a>
    <a href="#" style="left:754px">RESERVATION</a>
    <a href="#" style="left:884px">TAKEOUT</a>
    <a href="#" style="left:1010px">GIFT CARDS</a>
    <a href="#" style="left:1136px">CONTACT</a>
    <span class="underline"></span>
  </nav>
  <div class="abs hero-frame"></div>
  <div class="abs head center hero-kicker">Welcome to Lumbra</div>
  <div class="abs head center hero-title">Ember Oven Kitchen</div>
  <div class="abs btn-red hero-btn">Reservation</div>
  <div class="abs slide-arrow" style="left:31px;top:331px"><svg width="16" height="16" viewBox="0 0 16 16"><path d="M10 2 4 8l6 6" fill="none" stroke="#222" stroke-width="2"/></svg></div>
  <div class="abs slide-arrow" style="left:1102px;top:331px"><svg width="16" height="16" viewBox="0 0 16 16"><path d="M6 2l6 6-6 6" fill="none" stroke="#222" stroke-width="2"/></svg></div>

  <!-- Take out copy -->
  <h2 class="abs head center takeout-title">Take Out</h2>
  <span class="rule red" style="left:846px;top:930px;width:80px"></span>
  <div class="abs body-copy center takeout-copy">
    <p>Lorem Ipsum is simply dummy text of the printing and typesetting industry. Lorem Ipsum has been the industry's standard dummy text ever since the 1500s.</p>
    <p>when an unknown printer took a galley of type and scrambled it to make a type specimen book. It has survived not only five centuries, but also the leap into electronic typesetting.</p>
  </div>
  <div class="abs btn-outline takeout-btn">Book Now</div>

  <!-- Our Menu -->
  <div class="abs menu-band"></div>
  <h2 class="abs head center menu-title">Our Menu</h2>
  <span class="rule light" style="left:530px;top:1372px;width:140px"></span>
  <div class="abs menu-card" style="left:93px"><div class="photo" role="img" aria-label="Photo of grilled sandwich with greens" style="background:linear-gradient(160deg,#5a4a3c,#c9b79a 50%,#3f5f2a)"></div><div class="label">Sandwiches<i></i></div></div>
  <div class="abs menu-card" style="left:350px"><div class="photo" role="img" aria-label="Photo of bowls of dips and pasta" style="background:linear-gradient(160deg,#3b3b3b,#7d8a3c 45%,#c4893a)"></div><div class="label">Mains &amp; Pasta<i></i></div></div>
  <div class="abs menu-card" style="left:605px"><div class="photo" role="img" aria-label="Photo of a stacked burger" style="background:linear-gradient(160deg,#8a3a2a,#c98a4a 45%,#4a2a1e)"></div><div class="label">Burgers<i></i></div></div>
  <div class="abs menu-card" style="left:862px"><div class="photo" role="img" aria-label="Photo of wood fired pizzas" style="background:linear-gradient(160deg,#d9c7a8,#c4582e 45%,#e3c48a)"></div><div class="label">Ember Oven Pizza<i></i></div></div>
  <div class="abs menu-btn">View All Our Menu</div>

  <!-- Reservation -->
  <div class="abs res-dark"></div>
  <div class="abs res-photo" role="img" aria-label="Photo of the restaurant interior with bar and open kitchen"></div>
  <h2 class="abs head center res-title">Book Reservation</h2>
  <span class="rule light" style="left:278px;top:2026px;width:120px"></span>
  <div class="abs body-copy center res-copy">
    <p>Lorem Ipsum is simply dummy text of the printing and typesetting industry. Lorem Ipsum has been the industry's standard dummy text ever since the 1500s.</p>
    <p>when an unknown printer took a galley of type and scrambled it to make a type specimen book.</p>
  </div>
  <div class="abs btn-red res-btn">Book Now</div>

  <!-- Gift cards -->
  <h2 class="abs head center gift-title">Gift Cards</h2>
  <span class="rule red" style="left:510px;top:2506px;width:180px"></span>
  <div class="abs gift-card" style="left:128px;top:2545px"><div class="voucher" role="img" aria-label="Gold gift voucher with ribbon bow" style="background:linear-gradient(120deg,#b8902e,#f1d98a 50%,#c9a94e)"></div><h3>Gift Card Voucher</h3><p>Lorem Ipsum is simply dummy text of the printing and typesetting industry.</p></div>
  <div class="abs gift-card" style="left:457px;top:2556px"><div class="voucher" role="img" aria-label="Red gift voucher with ribbon bow" style="background:linear-gradient(120deg,#7a0a0c,#d11a1e 50%,#8c0c0e)"></div><h3>Gift Card Voucher</h3><p>Lorem Ipsum is simply dummy text of the printing and typesetting industry.</p></div>
  <div class="abs gift-card" style="left:777px;top:2556px"><div class="voucher" role="img" aria-label="Red glitter gift card with gold bow" style="background:linear-gradient(120deg,#c0101a,#e54a52 45%,#f0e3c0 55%,#c0101a)"></div><h3>Gift Card Voucher</h3><p>Lorem Ipsum is simply dummy text of the printing and typesetting industry.</p></div>
  <svg class="abs dots" width="112" height="4" viewBox="0 0 112 4" aria-hidden="true"><rect width="48" height="3" fill="#e0090d"/><rect x="62" width="48" height="2" fill="#9aa4b8"/></svg>

  <!-- Testimonials -->
  <div class="abs testi-band"></div>
  <h2 class="abs head center testi-title">Testimonials</h2>
  <span class="rule red" style="left:520px;top:3052px;width:170px"></span>
  <svg class="abs" style="left:80px;top:3220px" width="22" height="34" viewBox="0 0 22 34" aria-hidden="true"><path d="M18 2 4 17l14 15" fill="none" stroke="#999" stroke-width="2"/></svg>
  <svg class="abs" style="left:1097px;top:3220px" width="22" height="34" viewBox="0 0 22 34" aria-hidden="true"><path d="M4 2l14 15L4 32" fill="none" stroke="#999" stroke-width="2"/></svg>
  <div class="abs testi-card" style="left:130px"><svg width="38" height="28" viewBox="0 0 38 28" aria-hidden="true"><path d="M16 3C8 4 3 9 3 16a7 7 0 1 0 7-7M35 3c-8 1-13 6-13 13a7 7 0 1 0 7-7" fill="none" stroke="#e0090d" stroke-width="2"/></svg><h4>It Really tasty!</h4><p>Lorem Ipsum is simply dummy text of the printing and typesetting industry. Lorem Ipsum has been the industry's standard dummy text ever since</p><div class="who">Mara Quill</div><div class="stars">★★★★★</div></div>
  <div class="abs testi-card" style="left:453px;top:3113px"><svg width="38" height="28" viewBox="0 0 38 28" aria-hidden="true"><path d="M16 3C8 4 3 9 3 16a7 7 0 1 0 7-7M35 3c-8 1-13 6-13 13a7 7 0 1 0 7-7" fill="none" stroke="#e0090d" stroke-width="2"/></svg><h4>It Really tasty!</h4><p>Lorem Ipsum is simply dummy text of the printing and typesetting industry. Lorem Ipsum has been the industry's standard dummy text ever since</p><div class="who">Mara Quill</div><div class="stars">★★★★★</div></div>
  <div class="abs testi-card" style="left:773px"><svg width="38" height="28" viewBox="0 0 38 28" aria-hidden="true"><path d="M16 3C8 4 3 9 3 16a7 7 0 1 0 7-7M35 3c-8 1-13 6-13 13a7 7 0 1 0 7-7" fill="none" stroke="#e0090d" stroke-width="2"/></svg><h4>It Really tasty!</h4><p>Lorem Ipsum is simply dummy text of the printing and typesetting industry. Lorem Ipsum has been the industry's standard dummy text ever since</p><div class="who">Mara Quill</div><div class="stars">★★★★★</div></div>

  <!-- Contact -->
  <div class="abs contact-photo" role="img" aria-label="Photo of the restaurant team in front of the oven"></div>
  <svg class="abs contact-red" width="1200" height="560" viewBox="0 0 1200 560" aria-hidden="true">
    <defs><linearGradient id="contactFill" x1="0" y1="0" x2="1" y2="1"><stop offset="0" stop-color="#e40a0f"/><stop offset="1" stop-color="#a10a0c"/></linearGradient></defs>
    <polygon points="640,0 504,308 640,560 650,560 514,308 650,0" fill="#f3c9c9" opacity=".8"/>
    <polygon points="660,0 1200,0 1200,560 660,560 524,308" fill="url(#contactFill)"/>
  </svg>
  <h2 class="abs head contact-title">Contact Us</h2>
  <div class="abs contact-lines">
    <div>48 Fenwick Row, Bexwell 20417</div>
    <div>(555) 014 2290</div>
    <div class="gap"></div>
    <div>Monday to Thursday – 10pm till late</div>
    <div>Friday and Saturday – 12pm till midnight</div>
    <div>Sun – 12pm till 10pm</div>
    <div>Public Holidays – Closed</div>
  </div>
  <div class="abs contact-btn">Book Now</div>

  <!-- Footer -->
  <footer class="abs footer"></footer>
  <div class="abs to-top"><svg width="14" height="16" viewBox="0 0 14 16" aria-hidden="true"><path d="M7 15V2M2 7l5-5 5 5" fill="none" stroke="#fff" stroke-width="1.6"/></svg></div>
  <div class="abs logo foot-logo"><div class="name">LUMBRA</div><div class="sub">Ember Oven Kitchen</div></div>
  <span class="abs social" style="left:177px"></span>
  <span class="abs social" style="left:222px"></span>
  <span class="abs social" style="left:268px"></span>

  <div class="abs foot-col" style="left:413px;top:4105px"><h5>Navigation</h5><span class="underrule"></span><ul><li>Our Menu</li><li>Gift Cards</li><li>Reservation</li><li>Takeout</li><li>Contact Us</li></ul></div>
  <div class="abs foot-col" style="left:605px;top:4105px"><h5>Working Hours</h5><span class="underrule"></span><ul><li>Thursday, July 1st - &nbsp;Open</li><li>Friday, July 2nd - &nbsp;Open</li><li>Saturday, July 3rd - &nbsp;Open</li><li>Sunday, July 4th - &nbsp;Closed</li></ul></div>
  <div class="abs foot-col" style="left:854px;top:4105px"><h5>Contact Us</h5><span class="underrule"></span><ul>
    <li style="font-weight:700;color:#ddd;font-size:11px">LUMBRA</li>
    <li class="small"><svg width="12" height="15" viewBox="0 0 12 15"><path d="M6 14s5-5.5 5-8.5a5 5 0 0 0-10 0C1 8.5 6 14 6 14z" fill="#e0090d"/><circle cx="6" cy="5.5" r="1.8" fill="#1f1f1f"/></svg>48 Fenwick Row | Bexwell | 20417</li>
    <li class="small"><svg width="12" height="12" viewBox="0 0 12 12"><path d="M3 1 5 4 4 5.5c.8 1.3 1.6 2.1 2.5 2.5L8 7l3 2-1 2C5 11 1 7 1 2z" fill="#e0090d"/></svg>Phone: 555-014-2291</li>
    <li class="small"><svg width="13" height="10" viewBox="0 0 13 10"><rect x=".5" y=".5" width="12" height="9" fill="none" stroke="#e0090d"/><path d="M.5.5l6 5 6-5" fill="none" stroke="#e0090d"/></svg>Email: hello@lumbrabexwell.example</li>
  </ul></div>
  <div class="abs foot-rule"></div>
  <div class="abs copyright">Copyright © 2021 Lumbra All Right Reserved</div>
  <div class="abs legal" style="left:760px">Contact Us</div>
  <div class="abs legal" style="left:853px">Terms &amp; Conditions</div>
  <div class="abs legal" style="left:994px">Privacy Policy</div>

</div>
</body>
</html>
```